Kestrel Baseball & Softball Camp 2017

Design a flyer that will promote our 2017 summer camp for boys and girls softball.

Weeks of
July 10th - 14th
July 17th - 21st.

Players ages 5 - 11.
Full day = 9:30am - 2:30pm half day = 9:30am - 11:30am.
$295 / full day : $195/ half day

Hosted by "Kestrel Baseball" affiliated with the Harbor Comets Travel Baseball & Softball Club and the Maple Ridge Youth League,

Camp Location MRYL, Route 9C Birch Hollow.

PHone 555-240-7813, email info@kestrelball.example

The color should be "Red white and blue color scheme" with dates and location standing out. Kestrel Logo should be prominent MRYL and Comets smaller and secondary.

Feel free to use stock photo's if available. visit www.harborcomets.example for more pictures and there are links for the 2017 summer camp there with possibly some more information.

Target Market(s)

to catch the eye of parents of players ages 5 - 11 already at little league or shopping in local stores

Colors
ec1f27
0355a3
ffffff

Requirements
Must have
• red white and blue design,
• Kestrel logo and summer camp prominent so it catches the eye and explains what it is right away.
• the comets and maple ridge logo's a the bottom showing the affiliation.
Nice to have
• stock photo's or something showing players having a great time or a beautiful ballpark
Should not have
• to much clutter or hard to figure out what it's for

```html
<!DOCTYPE html>
<html lang="en">
<head>
<meta charset="utf-8">
<title>Kestrel Softball Summer Camp 2017</title>
<link rel="stylesheet" href="https://fonts.googleapis.com/css2?family=Anton&family=Kaushan+Script&family=Oswald:wght@500;700&family=Pacifico&display=swap">
<style>
:root{
  --red:#d9262c;
  --navy:#1f3a6b;
  --white:#ffffff;
  --sky-top:#3f7fc4;
  --sky-low:#a9c3d9;
  --stands:#7c8696;
  --grass-top:#b9cfa8;
  --grass-low:#dfe6cf;
  --dirt-top:#f2c8a8;
  --dirt-low:#e9b995;
  --ink:#1d1d1d;
  --dash:#8a8a8a;
  --register:#d3533b;
}
*{margin:0;padding:0;box-sizing:border-box}
html,body{width:817px;height:1200px;overflow:hidden;background:var(--white)}
.flyer{position:relative;width:817px;height:1200px;overflow:hidden;font-family:"Oswald",sans-serif}
.ballpark{position:absolute;left:0;top:0;width:817px;height:545px;
  background:linear-gradient(180deg,var(--sky-top) 0%,var(--sky-low) 30%,var(--stands) 48%,#8f96a0 75%,#a7ad9c 100%)}
.field{position:absolute;left:0;top:545px;width:817px;height:335px;
  background:linear-gradient(180deg,var(--grass-top) 0%,var(--grass-low) 100%)}
.affiliation{position:absolute;left:0;top:880px;width:817px;height:118px;background:var(--white)}
.infield{position:absolute;left:0;top:998px;width:817px;height:202px;
  background:linear-gradient(180deg,var(--dirt-top),var(--dirt-low))}
.rule-dash{position:absolute;left:34px;width:750px;border-top:2px dashed var(--dash)}
.rule-solid{position:absolute;left:34px;width:750px;border-top:2px solid var(--ink)}
.logo-tab{position:absolute;left:0;top:0}
.brand{position:absolute;left:274px;top:0;width:267px;height:250px;display:flex;flex-direction:column;align-items:center;justify-content:center;gap:10px}
.brand-dot{width:70px;height:70px;border-radius:50%;background:var(--red)}
.brand-name{font-family:"Anton",sans-serif;font-size:44px;color:var(--red);letter-spacing:1px}
.script-softball{position:absolute;left:62px;top:300px;font-family:"Pacifico",cursive;font-size:44px;color:var(--white)}
.headline{position:absolute;left:50px;top:350px;font-family:"Anton",sans-serif;font-size:136px;line-height:1;letter-spacing:-1px;white-space:nowrap;transform:scaleX(0.86);transform-origin:left top}
.headline .summer{color:var(--red)}
.headline .camp{color:var(--white)}
.year{position:absolute;left:760px;top:368px;transform:rotate(90deg);transform-origin:left top;font-family:"Anton",sans-serif;font-size:54px;color:var(--white);line-height:1;white-space:nowrap}
.tagline{position:absolute;left:492px;top:486px;font-family:"Pacifico",cursive;font-size:18px;color:var(--white)}
.weeks{position:absolute;left:80px;top:556px;font-weight:700;font-size:31px;line-height:50px;color:var(--navy);text-transform:uppercase}
.players{position:absolute;left:428px;top:603px;display:flex;gap:10px;color:var(--navy)}
.players-label{font-weight:700;font-size:31px;line-height:48px;text-transform:uppercase}
.age-badge{position:absolute;left:602px;top:579px;width:132px;height:132px;border-radius:50%;background:var(--navy);color:var(--white);display:flex;align-items:center;justify-content:center;font-weight:500;font-size:36px}
.hours{position:absolute;left:68px;top:772px;display:flex;gap:12px;color:var(--red)}
.hours-text{font-weight:700;font-size:22px;line-height:33px;text-transform:uppercase}
.cost{position:absolute;left:440px;top:772px;display:flex;align-items:center;gap:10px;color:var(--navy)}
.cost-label{font-family:"Kaushan Script",cursive;font-size:20px}
.cost-icon{width:34px;height:34px;border-radius:50%;background:var(--navy);color:var(--white);display:flex;align-items:center;justify-content:center;font-weight:700;font-size:21px}
.cost-text{font-weight:700;font-size:22px;line-height:33px;text-transform:uppercase;margin-left:4px}
.host{position:absolute;left:46px;top:902px;font-weight:500;font-size:11.5px;line-height:17px;color:var(--ink);text-transform:uppercase}
.partner{position:absolute;display:flex;align-items:center;font-weight:700;text-transform:uppercase}
.partner-comets{left:524px;top:902px;font-size:34px;line-height:48px;color:var(--red)}
.partner-maple{left:688px;top:888px;flex-direction:column;gap:4px;font-size:11px;color:var(--navy);text-align:center}
.partner-shape{width:62px;height:62px;background:var(--white);border:2px solid var(--navy);border-radius:50%}
.register{position:absolute;left:64px;top:1022px;transform:rotate(-10deg);font-family:"Kaushan Script",cursive;font-size:40px;line-height:48px;color:var(--register)}
.info-block{position:absolute;top:1022px}
.info-location{left:258px}
.info-contact{left:510px}
.info-head{display:flex;align-items:center;gap:10px;font-family:"Kaushan Script",cursive;font-size:20px;color:var(--navy)}
.info-body{margin-left:28px;margin-top:6px;font-weight:700;font-size:18px;line-height:28px;color:var(--ink);text-transform:uppercase}
</style>
</head>
<body>
<main class="flyer">
  <div class="ballpark" role="img" aria-label="Blurred photo of a sunny ballpark with blue sky and grandstands"></div>
  <div class="field" role="img" aria-label="Blurred photo of a green outfield with a pitcher's mound"></div>
  <div class="affiliation"></div>
  <div class="infield" role="img" aria-label="Photo of infield dirt"></div>

  <svg class="logo-tab" width="817" height="290" viewBox="0 0 817 290" aria-hidden="true">
    <polygon points="274,0 541,0 541,250 407,282 274,250" fill="#ffffff"/>
  </svg>
  <div class="brand">
    <span class="brand-dot"></span>
    <span class="brand-name">Kestrel</span>
  </div>

  <p class="script-softball">softball</p>
  <h1 class="headline"><span class="summer">SUMMER</span><span class="camp">CAMP</span></h1>
  <p class="year">2017</p>
  <p class="tagline">for boys and girls</p>

  <p class="weeks">Weeks of<br>July 10th - 14th<br>July 17th - 21st.</p>

  <div class="players">
    <svg width="40" height="40" viewBox="0 0 40 40" aria-hidden="true" style="margin-top:6px">
      <circle cx="11" cy="6" r="4" fill="#1f3a6b"/><rect x="6" y="12" width="10" height="14" rx="2" fill="#1f3a6b"/><rect x="7" y="25" width="3.5" height="12" fill="#1f3a6b"/><rect x="11.5" y="25" width="3.5" height="12" fill="#1f3a6b"/>
      <circle cx="29" cy="6" r="4" fill="#1f3a6b"/><polygon points="24,12 34,12 37,28 21,28" fill="#1f3a6b"/><rect x="25" y="27" width="3" height="10" fill="#1f3a6b"/><rect x="30" y="27" width="3" height="10" fill="#1f3a6b"/>
    </svg>
    <p class="players-label">Players<br>Ages</p>
  </div>
  <div class="age-badge">5 - 11</div>

  <div class="hours">
    <svg width="30" height="34" viewBox="0 0 30 34" aria-hidden="true" style="margin-top:10px">
      <rect x="11" y="0" width="8" height="4" fill="#d9262c"/><circle cx="15" cy="19" r="12" fill="none" stroke="#d9262c" stroke-width="3.5"/><line x1="15" y1="19" x2="15" y2="12" stroke="#d9262c" stroke-width="3"/>
    </svg>
    <p class="hours-text">Full day = 9:30am - 2:30pm<br>Half day = 9:30am - 11:30am.</p>
  </div>

  <div class="cost">
    <span class="cost-label">Cost:</span>
    <span class="cost-icon">$</span>
    <p class="cost-text">$295 / full day<br>$195/ half day</p>
  </div>

  <div class="rule-dash" style="top:879px"></div>
  <p class="host">Hosted by "Kestrel Baseball"<br>affiliated with the Harbor Comets Travel Baseball &amp; Softball Club and<br>the Maple Ridge Youth League</p>
  <div class="partner partner-comets">Comets</div>
  <div class="partner partner-maple"><span class="partner-shape"></span>Maple Ridge</div>
  <div class="rule-solid" style="top:975px"></div>
  <div class="rule-dash" style="top:992px"></div>

  <p class="register">Register<br>today!</p>

  <div class="info-block info-location">
    <p class="info-head">
      <svg width="16" height="22" viewBox="0 0 16 22" aria-hidden="true"><path d="M8 0C3.6 0 0 3.5 0 8c0 5.5 8 14 8 14s8-8.5 8-14c0-4.5-3.6-8-8-8z" fill="#1f3a6b"/><circle cx="8" cy="8" r="3" fill="#f2c8a8"/></svg>
      Camp Location:
    </p>
    <p class="info-body">Camp location MRYL,<br>Route 9C Birch Hollow.</p>
  </div>

  <div class="info-block info-contact">
    <p class="info-head">
      <svg width="16" height="26" viewBox="0 0 16 26" aria-hidden="true"><rect x="3" y="0" width="2" height="6" fill="#1f3a6b"/><rect x="1" y="5" width="14" height="21" rx="3" fill="#1f3a6b"/><rect x="4" y="9" width="8" height="6" fill="#f2c8a8"/></svg>
      Contact:
    </p>
    <p class="info-body">Phone 555-240-7813, email<br>info@kestrelball.example</p>
  </div>
</main>
</body>
</html>
```